Silver Bloom Marisol's Cleaning Service Business Cards Project

A business card with all contact details with logo design on there (already have a logo) eye catching Logo and contact info on one side, full logo on the back, must target upper class residential and corporate companies, fitness companies, still keep it on the feminine side of things , must look elegant

Target Market(s)

Upper class homes and corporate companies

Industry/Entity Type

Cleaning Service

Contact Information for Business Card

Name: Marisol Quenby
Position: Director
ABN: 31647209853
Email: marisolssilvercleaning@tidymail.example
Number: 0417906354

Font styles to use
Decorative

Colors

Designer to choose colors to be used in the design.

Requirements
Must have
• Available Sydney Wide, contact info and logo on one side, full logo on the back
Nice to have
• Professional appearance
Should not have
• Cheap advert looking stuff

```html
<!DOCTYPE html>
<html lang="en">
<head>
<meta charset="utf-8">
<title>Silver Bloom – Business Cards</title>
<link rel="stylesheet" href="https://fonts.googleapis.com/css2?family=Cinzel:wght@500;700&family=Montserrat:wght@400;500&family=Oswald:wght@500&family=Roboto:wght@400&display=swap">
<style>
  :root {
    --navy: #2f3446;
    --navy-soft: #3a4056;
    --teal: #5cc3c6;
    --teal-light: #a8e0e1;
    --white: #ffffff;
    --stage: #e9e8e6;
    --muted: #c9ccd6;
  }
  * { margin: 0; padding: 0; box-sizing: border-box; }
  html, body { width: 1200px; height: 930px; overflow: hidden; }
  body { background: var(--stage); position: relative; }

  .card {
    position: absolute;
    width: 700px;
    height: 400px;
    border-radius: 18px;
    overflow: hidden;
    box-shadow: 0 6px 18px rgba(0,0,0,0.18);
  }

  /* Back of card */
  .card-back { left: 90px; top: 50px; background: var(--navy); }
  .card-back .pattern {
    position: absolute; inset: 0;
    background: radial-gradient(circle at 50% 50%, var(--navy-soft), var(--navy) 75%);
  }
  .card-back .brand {
    position: absolute; left: 0; right: 0; top: 150px;
    text-align: center; color: var(--white);
  }
  .brand-name {
    font-family: "Cinzel", serif;
    font-weight: 700;
    font-size: 52px;
    letter-spacing: 2px;
  }
  .brand-tagline {
    font-family: "Montserrat", sans-serif;
    font-weight: 400;
    font-size: 15px;
    letter-spacing: 6px;
    margin-top: 8px;
  }

  /* Front of card */
  .card-front { left: 410px; top: 480px; background: var(--white); }
  .card-front svg.shapes { position: absolute; inset: 0; }
  .front-brand {
    position: absolute; left: 180px; width: 240px; top: 36px;
    text-align: center; color: var(--navy);
  }
  .front-brand .mark {
    width: 40px; height: 40px; border: 2px solid var(--navy);
    border-radius: 50%; margin: 0 auto 10px;
  }
  .front-brand .brand-name { font-size: 24px; letter-spacing: 1px; }
  .front-brand .brand-tagline { font-size: 7px; letter-spacing: 2.5px; margin-top: 3px; }

  .person {
    position: absolute; left: 36px; top: 318px; color: var(--white);
  }
  .person-name {
    font-family: "Oswald", sans-serif; font-weight: 500;
    font-size: 40px; letter-spacing: 2px; line-height: 1;
  }
  .person-role {
    font-family: "Roboto", sans-serif; font-size: 15px;
    text-align: right; margin-top: 2px;
  }
  .divider {
    position: absolute; left: 356px; top: 286px;
    width: 1.5px; height: 90px; background: var(--white);
  }
  .contacts {
    position: absolute; left: 376px; top: 288px;
    list-style: none; color: var(--white);
    font-family: "Roboto", sans-serif; font-size: 14px;
  }
  .contacts li { display: flex; align-items: center; gap: 8px; height: 27px; }
  .contacts svg { width: 12px; height: 12px; flex: none; }
</style>
</head>
<body>

<section class="card card-back">
  <div class="pattern" role="img" aria-label="Faint repeating gem pattern across the card"></div>
  <div class="brand">
    <div class="brand-name">SILVER BLOOM</div>
    <div class="brand-tagline">MARISOL'S CLEANING SERVICES</div>
  </div>
</section>

<section class="card card-front">
  <svg class="shapes" viewBox="0 0 700 400" width="700" height="400">
    <defs>
      <linearGradient id="vine-tone" x1="0" y1="0" x2="1" y2="0">
        <stop offset="0" stop-color="var(--teal-light)"/>
        <stop offset="0.5" stop-color="var(--teal)"/>
        <stop offset="1" stop-color="var(--teal-light)"/>
      </linearGradient>
    </defs>
    <path role="img" aria-label="Teal flourishing vine ornament along the wave"
          fill="url(#vine-tone)" opacity="0.85"
          d="M0,205 C80,185 110,265 200,255 C300,245 330,170 430,180 C520,190 540,120 620,100 C660,90 690,95 700,70 L700,400 L0,400 Z"/>
    <path fill="var(--white)"
          d="M0,228 C80,208 110,288 200,278 C300,268 330,198 430,208 C520,218 540,148 620,128 C660,118 690,123 700,98 L700,400 L0,400 Z"/>
    <path fill="var(--navy)"
          d="M0,240 C80,220 110,300 200,290 C300,280 330,210 430,220 C520,230 540,160 620,140 C660,130 690,135 700,110 L700,400 L0,400 Z"/>
  </svg>

  <div class="front-brand">
    <div class="mark"></div>
    <div class="brand-name">SILVER BLOOM</div>
    <div class="brand-tagline">MARISOL'S CLEANING SERVICES</div>
  </div>

  <div class="person">
    <div class="person-name">MARISOL QUENBY</div>
    <div class="person-role">Director</div>
  </div>

  <div class="divider"></div>

  <ul class="contacts">
    <li>ABN: 31647209853</li>
    <li>
      <svg viewBox="0 0 24 24" aria-hidden="true"><path fill="var(--white)" d="M6.6 10.8a15.1 15.1 0 0 0 6.6 6.6l2.2-2.2a1 1 0 0 1 1-.25 11.4 11.4 0 0 0 3.6.57 1 1 0 0 1 1 1V20a1 1 0 0 1-1 1A17 17 0 0 1 3 4a1 1 0 0 1 1-1h3.5a1 1 0 0 1 1 1c0 1.25.2 2.45.57 3.57a1 1 0 0 1-.25 1z"/></svg>
      0417906354
    </li>
    <li>
      <svg viewBox="0 0 24 24" aria-hidden="true"><rect x="2.5" y="5" width="19" height="14" rx="1.5" fill="none" stroke="var(--white)" stroke-width="2"/><path d="M3 6l9 7 9-7" fill="none" stroke="var(--white)" stroke-width="2"/></svg>
      marisolssilvercleaning@tidymail.example
    </li>
  </ul>
</section>

</body>
</html>
```